Single-sided business card for restaurant velmora with new logo made on this site

Business card options with new logo including restaurant name, address, phone number and website. This business card is single-sided only and will be presented at the hostess desk for clients to take. I would like to see options based on a cream card background, a white card background, a yellow card background and a burgundy colored background. It needs to be elegant and traditional.

Target Market(s)

local and international crowd

Industry/Entity Type

restaurant

Contact Information for Business Card

address, website and phone number

Font styles to use
Serif

Colors
EE7325
F08F49
F5BC92
FAE3D3
FDF4ED

Requirements
Must have
• new logo, address, phone number, website
Should not have
• more than three colors

```html
<!DOCTYPE html>
<html lang="es">
<head>
<meta charset="utf-8">
<title>Velmora – Tarjeta de presentación</title>
<link href="https://fonts.googleapis.com/css2?family=Crimson+Pro:wght@400;600;700&display=swap" rel="stylesheet">
<style>
  :root {
    --backdrop: #9b9b9b;
    --card-yellow: #eeaa2a;
    --ink-brown: #3a1512;
    --leaf-dark: #0c0c0c;
    --leaf-mid: #4a4a4a;
    --leaf-light: #bdbdbd;
  }
  * { margin: 0; padding: 0; box-sizing: border-box; }
  html, body {
    width: 1200px;
    height: 1050px;
    overflow: hidden;
    background: var(--backdrop);
  }
  .business-card {
    position: absolute;
    left: 340px;
    top: 70px;
    width: 520px;
    height: 910px;
    background: var(--card-yellow);
    color: var(--ink-brown);
    font-family: "Crimson Pro", "Times New Roman", serif;
    overflow: hidden;
    box-shadow: 0 3px 0 var(--ink-brown);
  }
  .brand-lockup {
    position: absolute;
    top: 128px;
    left: 0;
    width: 100%;
    display: flex;
    justify-content: center;
    align-items: flex-end;
    gap: 16px;
  }
  .brand-square {
    width: 128px;
    height: 128px;
    background: var(--ink-brown);
  }
  .brand-text {
    display: flex;
    flex-direction: column;
    align-items: flex-start;
  }
  .brand-name {
    font-size: 40px;
    font-weight: 400;
    letter-spacing: 8px;
    line-height: 1;
    padding-bottom: 8px;
    border-bottom: 1.5px solid var(--ink-brown);
  }
  .brand-since {
    font-size: 10px;
    letter-spacing: 1px;
    margin-top: 5px;
    align-self: flex-end;
  }
  .contact-block {
    position: absolute;
    top: 320px;
    left: 0;
    width: 100%;
    text-align: center;
    line-height: 1.15;
  }
  .venue-name { font-size: 22px; font-weight: 700; }
  .venue-address { font-size: 23px; font-weight: 400; }
  .reservations-label { font-size: 22px; font-weight: 700; margin-top: 18px; }
  .reservations-phone {
    font-size: 27px;
    font-weight: 400;
    display: inline-flex;
    align-items: center;
    gap: 6px;
  }
  .reservations-phone svg { width: 18px; height: 18px; }
  .website {
    font-size: 21px;
    font-weight: 700;
    letter-spacing: 1px;
    margin-top: 12px;
  }
  .agave-area {
    position: absolute;
    left: 60px;
    right: 0;
    top: 560px;
    bottom: 0;
    background: linear-gradient(to bottom left, var(--leaf-dark) 0%, var(--leaf-mid) 50%, var(--leaf-light) 100%);
  }
</style>
</head>
<body>
  <div class="business-card">
    <div class="brand-lockup">
      <div class="brand-square"></div>
      <div class="brand-text">
        <span class="brand-name">VELMORA</span>
        <span class="brand-since">DESDE 1999</span>
      </div>
    </div>

    <div class="contact-block">
      <p class="venue-name">Restaurant Velmora</p>
      <p class="venue-address">Magnolia 418, Bahía Serena</p>
      <p class="venue-address">Oaxaca CP 70912</p>
      <p class="reservations-label">Reservaciones</p>
      <p class="reservations-phone">
        <svg viewBox="0 0 24 24" aria-hidden="true">
          <path d="M6.6 10.8a15 15 0 0 0 6.6 6.6l2.2-2.2a1 1 0 0 1 1-.25 11.4 11.4 0 0 0 3.6.57 1 1 0 0 1 1 1V20a1 1 0 0 1-1 1A17 17 0 0 1 3 4a1 1 0 0 1 1-1h3.5a1 1 0 0 1 1 1c0 1.25.2 2.45.57 3.6a1 1 0 0 1-.25 1z" fill="none" stroke="currentColor" stroke-width="1.6"/>
        </svg>
        958-555-0142
      </p>
      <p class="website">www.Velmora.com.mx</p>
    </div>

    <div class="agave-area" role="img" aria-label="Ilustración de hojas de agave en abanico, en degradado de negro a plateado"></div>
  </div>
</body>
</html>
```